Tellmora Corporate Stationery

Look for design of all new corporate stationery for an existing insurance broking business that is going through a redesign and move from older partners to younger family members. New Logo is attached. Company is Brisbane based.
Colours in the Logo is Hex #43bed8 and website features a lot of hex #17b8d8. Website front page "A plan to protect you" - headline. "Professional and Individual advice to protect your greatest assets" - tagline.

Stationery required: Business Cards, Letter head, Thank-you cards, Birthday cards, Presentation folders, With Compliment slips and a powerpoint template. We also would like to send a card to all customers with the something along of the lines of "something new".

Target Market(s)

Customers of Insurance business looking at superannuation, life and income protection insurance, investment advice and wills

Industry/Entity Type

Insurance Broker

Font styles to use
Other font styles liked:
• same as logo

Requirements
Must have
• The above designs for new stationery for the new business including:
• Business Cards, Letter head, Thank-you cards, Birthday cards, Presentation folders, With Compliment slips and a powerpoint template. We also would like to send a card to all customers with the something along of the lines of "something new".
Nice to have
• It is a new look - long time family business being passed to next generation - big focus on advice for YOU, individual advice etc..

```html
<!DOCTYPE html>
<html lang="en">
<head>
<meta charset="utf-8">
<title>Tellmora Presentation Folder</title>
<link rel="stylesheet" href="https://fonts.googleapis.com/css2?family=Michroma&display=swap">
<style>
  :root {
    --brand-blue: #40bdd8;
    --bar-grey: #808285;
    --paper: #ffffff;
    --band-edge: #e4e6e8;
    --canvas-bg: #ffffff;
  }
  html, body {
    margin: 0;
    padding: 0;
    width: 1200px;
    height: 1000px;
    overflow: hidden;
    background: var(--canvas-bg);
  }
  .folder {
    display: block;
    width: 1200px;
    height: 1000px;
  }
  .folder-cover { fill: var(--brand-blue); }
  .brand-band { fill: var(--paper); stroke: var(--band-edge); stroke-width: 1.5; }
  .pocket {
    fill: var(--brand-blue);
    filter: drop-shadow(2px 2px 3px rgba(0,0,0,0.18));
  }
  .seal { fill: var(--paper); }
  .text-bar { fill: var(--bar-grey); }
  .brand-name {
    font-family: "Michroma", sans-serif;
    font-size: 40px;
    letter-spacing: 2px;
    fill: var(--brand-blue);
  }
</style>
</head>
<body>
<svg class="folder" viewBox="0 0 1200 1000" xmlns="http://www.w3.org/2000/svg" aria-label="Tellmora presentation folder, flat die-cut">
  <!-- front cover -->
  <path class="folder-cover" d="M2,28 L45,20 H1200 V312 H2 Z"/>

  <!-- white brand band -->
  <rect class="brand-band" x="0" y="310" width="1197" height="100"/>

  <!-- inside pocket with business-card slot -->
  <path class="pocket" d="M0,408 H1157 V695 H1153 V718 Q1152,718 1152,722 V977 H670 Q648,977 642,955 L602,720 Q599,713 596,720 L557,955 Q551,977 530,977 H48 V728 Q48,705 0,705 Z"/>

  <!-- round seal on the band -->
  <circle class="seal" cx="876" cy="358" r="88"/>

  <!-- brand name -->
  <text class="brand-name" x="133" y="376">TELLMORA</text>

  <!-- content lines on pocket -->
  <g class="pocket-lines">
    <rect class="text-bar" x="132" y="556" width="935" height="20" rx="10"/>
    <rect class="text-bar" x="132" y="589" width="935" height="20" rx="10"/>
    <rect class="text-bar" x="132" y="621" width="935" height="20" rx="10"/>
    <rect class="text-bar" x="132" y="654" width="935" height="20" rx="10"/>
  </g>
</svg>
</body>
</html>
```